Web Design Project

Psychotherapy and Counselling Practice needs a landing page web design.

My business "Larkfield Advisory" specialises in the treatment of Anxiety and Depression with a holistic approach, endeavouring to unlock the key that holds us to ransom in a life that is imbalanced, frustrating, and ultimately of our own making due to our own perceptions and behaviours.

There is much that impacts us which we cannot change, but we are always in control of how we think, and how we frame our experiences.....learning to challenge those thoughts and behaviours that are destructive and disempowering opens up a world of joyful possibility. Life is about making choices, learn to make wiser and healthier choices.......

Larkfield Advisory has a client base of individual clients but will seek to expand to offer services to the Corporate world by offering an adjunct to employers for established "Wellness Programs".

Larkfield Advisory is a highly professional, ethically bound business, with the needs of the client at the forefront of all we do.

Larkfield Advisory wishes to avoid the usual "jargon driven" psychobabble offered on many counselling web pages. It aims to be stylishly presented, clean in look and with as few "words" as possible and a largely white background (faster loading and more powerful impact of what is stated), those words contained in the webpage should be meaningful, persuasive and have an impact simply at glance. Larkfield does not want , or expect, those prospective clients in need of support , to be reading through volumes of industry driven cliches.

At this point Larkfield is just looking for a high quality landing page. However in time this will likely expand to include other sections such as case studies, video content etc.

Target Market(s)

Those in need of emotional support, suffering mental health issues, and those simply wanting to become self aware supported by a mindful therapist.

Industry/Entity Type

Industry

Requirements
Must have
• The design must incorporate the Larkfield logo and colour schemes found on the attached files.

```html
<!DOCTYPE html>
<html lang="en">
<head>
<meta charset="utf-8">
<title>Larkfield Advisory – Counselling</title>
<link href="https://fonts.googleapis.com/css2?family=Mulish:wght@300;400;600;800&display=swap" rel="stylesheet">
<style>
  :root{
    --green:#8aa60b;
    --green-text:#8cb10e;
    --green-bright:#a9cc1a;
    --charcoal:#595958;
    --text:#555;
    --bg:#f4f4f4;
    --white:#fff;
  }
  *{box-sizing:border-box;margin:0;padding:0}
  html,body{width:1200px;height:942px;overflow:hidden}
  body{
    position:relative;
    background:radial-gradient(ellipse at 50% 30%,#fbfbfb 0%,var(--bg) 70%);
    font-family:"Mulish",sans-serif;color:var(--text);
  }
  .header-flourish{
    position:absolute;left:0;top:60px;width:1000px;height:232px;
    background:linear-gradient(180deg,rgba(138,166,11,0) 0%,rgba(138,166,11,.06) 60%,rgba(112,112,112,.08) 100%);
  }
  .brand{
    position:absolute;left:231px;top:100px;
    font-size:37px;font-weight:300;letter-spacing:1px;color:var(--green-text);
  }
  .contact{position:absolute;right:202px;top:76px;text-align:right}
  .contact__label{font-size:12.5px;color:#666}
  .contact__phone{font-size:29px;font-weight:400;color:#5a5a5a;line-height:1.05;display:flex;align-items:center;justify-content:flex-end;gap:3px}
  .contact__email{font-size:14px;color:var(--green-text)}

  .hero{position:absolute;left:199px;top:298px;width:801px;height:333px;display:flex;box-shadow:0 14px 14px -10px rgba(0,0,0,.18)}
  .enquiry{width:400px;background:var(--green);padding:14px 0 0 16px;position:relative}
  .enquiry__title{font-size:22px;font-weight:800;color:var(--white);letter-spacing:-.6px;margin:0 0 9px 1px}
  .field{width:353px;height:36px;background:var(--white);display:flex;align-items:center;margin-bottom:7px;border:1px solid #e3e3e3}
  .field--message{height:99px;align-items:flex-start;padding-top:8px;margin-top:2px}
  .field__icon{width:37px;height:20px;display:flex;justify-content:center;align-items:center;border-right:1px solid #ccc}
  .field__text{padding-left:10px;font-size:14px;color:#777;font-weight:400}
  .send{position:absolute;left:345px;bottom:22px}
  .promise{flex:1;background:var(--charcoal);color:var(--white);padding:126px 0 0 42px;font-weight:300}
  .promise p{line-height:1.1}
  .promise__l1{font-size:19px}
  .promise__l2{font-size:19px}
  .promise__l2 span{color:var(--green-bright);font-size:22px;font-weight:400}
  .promise__l3{font-size:15px}
  .promise__l3 span{font-size:27px}

  .feature{position:absolute;top:682px}
  .feature__head{display:flex;align-items:center;gap:12px;font-size:19px;color:var(--green-text);font-weight:400}
  .feature__body{margin-top:14px;width:205px;font-size:10.3px;line-height:13.5px;color:#666}
  .feature__more{display:block;margin-top:18px;font-size:11.5px;color:#444;text-decoration:none}
  .divider{position:absolute;top:688px;height:143px;border-left:1px dotted #bbb}
  .video{position:absolute;left:752px;top:726px;width:239px;height:108px;border:2px solid #ddd;
    background:repeating-linear-gradient(90deg,#efefef 0 6px,#e8e8e8 6px 12px);
    display:flex;align-items:center;justify-content:center;gap:10px}
  .video__name{font-size:22px;font-weight:300;color:var(--green-text);letter-spacing:.5px}

  .footer{position:absolute;left:202px;top:878px;width:796px;border-top:1px dotted #aaa;padding-top:20px;display:flex;justify-content:space-between;align-items:center}
  .footer__copy{font-size:11.5px;color:#666}
  .footer__copy span{color:var(--green-text);font-size:14px;letter-spacing:-.3px}
  .social{display:flex;gap:6px}
  .social__item{width:12px;height:12px;border-radius:2px;background:#777}
</style>
</head>
<body>

<div class="header-flourish" role="img" aria-label="Decorative header flourish"></div>

<div class="brand">LARKFIELD</div>

<div class="contact">
  <p class="contact__label">For Appointmet Call Us Today</p>
  <p class="contact__phone">
    <svg width="22" height="22" viewBox="0 0 24 24"><path fill="#8cb10e" d="M6.6 10.8a15 15 0 0 0 6.6 6.6l2.2-2.2c.3-.3.7-.4 1-.2 1.1.4 2.3.6 3.6.6.6 0 1 .4 1 1V20c0 .6-.4 1-1 1A17 17 0 0 1 3 4c0-.6.4-1 1-1h3.5c.6 0 1 .4 1 1 0 1.3.2 2.5.6 3.6.1.3 0 .7-.2 1z"/></svg>
    0400 218 657
  </p>
  <p class="contact__email">mara.holt@larkmail.net</p>
</div>

<section class="hero">
  <form class="enquiry">
    <h2 class="enquiry__title">GET MORE INFORMATION</h2>
    <div class="field"><span class="field__icon"><svg width="16" height="18" viewBox="0 0 16 18"><circle cx="8" cy="4.5" r="4" fill="#666"/><path d="M0 18c0-6 3-8.5 8-8.5s8 2.5 8 8.5z" fill="#666"/></svg></span><span class="field__text">Enter Your Name</span></div>
    <div class="field"><span class="field__icon"><svg width="22" height="16" viewBox="0 0 22 16"><rect x="1" y="4" width="20" height="11" fill="none" stroke="#666" stroke-width="1.6"/><path d="M1 4l10 7 10-7M1 4l10-3 10 3" fill="none" stroke="#666" stroke-width="1.6"/></svg></span><span class="field__text">Enter Your Email</span></div>
    <div class="field"><span class="field__icon"><svg width="16" height="16" viewBox="0 0 24 24"><path fill="#666" d="M6.6 10.8a15 15 0 0 0 6.6 6.6l2.2-2.2c.3-.3.7-.4 1-.2 1.1.4 2.3.6 3.6.6.6 0 1 .4 1 1V20c0 .6-.4 1-1 1A17 17 0 0 1 3 4c0-.6.4-1 1-1h3.5c.6 0 1 .4 1 1 0 1.3.2 2.5.6 3.6.1.3 0 .7-.2 1z"/></svg></span><span class="field__text">Enter Your Phone</span></div>
    <div class="field field--message"><span class="field__icon"><svg width="16" height="18" viewBox="0 0 16 18"><rect x="1" y="2" width="12" height="15" fill="none" stroke="#666" stroke-width="1.4"/><path d="M6 14l1-3 7-7 2 2-7 7z" fill="#666"/></svg></span><span class="field__text">Your Message Here...</span></div>
    <svg class="send" width="22" height="16" viewBox="0 0 22 16"><path d="M2 1l8 7-8 7M10 1l8 7-8 7" fill="none" stroke="#fff" stroke-width="2.6"/></svg>
  </form>
  <div class="promise">
    <p class="promise__l1">SPECIALISES IN THE TREATMENT</p>
    <p class="promise__l2">OF <span>ANXIETY AND DEPRESSION</span></p>
    <p class="promise__l3">WITH <span>HOLISTIC APPROACH</span></p>
  </div>
</section>

<article class="feature" style="left:212px">
  <h3 class="feature__head"><svg width="28" height="24" viewBox="0 0 28 24"><path d="M14 23L2.5 11.5A6.5 6.5 0 0 1 14 3.5a6.5 6.5 0 0 1 11.5 8z" fill="#666"/><path d="M3 11h7l2-3 3 6 2-3h8" fill="none" stroke="#f4f4f4" stroke-width="1.3"/></svg>Wellness Programs</h3>
  <p class="feature__body">Lorem ipsum dolor sit amet, consectetuer adipiscing elit, sed diam nonummy nibh euismod tincidunt ut laoreet dolore magna aliquam erat volutpat. Ut wisi enim ad minim veniam, quis nostrud exerci tation ullamcorper suscipit lobortis...</p>
  <a class="feature__more" href="#">Read More...</a>
</article>
<div class="divider" style="left:452px"></div>
<article class="feature" style="left:490px">
  <h3 class="feature__head"><svg width="28" height="22" viewBox="0 0 28 22"><path d="M14 4C10 1 5 1 1 2v17c4-1 9-1 13 2 4-3 9-3 13-2V2c-4-1-9-1-13 2z" fill="none" stroke="#666" stroke-width="2"/><path d="M14 4v17M4 7h7M4 11h7M4 15h7M17 7h7M17 11h7M17 15h7" stroke="#666" stroke-width="1.3"/></svg>Case Studies</h3>
  <p class="feature__body">Lorem ipsum dolor sit amet, consectetuer adipiscing elit, sed diam nonummy nibh euismod tincidunt ut laoreet dolore magna aliquam erat volutpat. Ut wisi enim ad minim veniam, quis nostrud exerci tation ullamcorper suscipit lobortis...</p>
  <a class="feature__more" href="#">Read More...</a>
</article>
<div class="divider" style="left:722px"></div>
<article class="feature" style="left:753px">
  <h3 class="feature__head"><svg width="24" height="22" viewBox="0 0 24 22"><rect x="1" y="7" width="22" height="14" fill="#666"/><path d="M1 2l21-1 .5 4.5-21 1z" fill="#666"/><path d="M5 2l2 4M10 2l2 4M15 1.5l2 4" stroke="#f4f4f4" stroke-width="1.5"/></svg>Watch Video</h3>
</article>
<div class="video" role="img" aria-label="Introductory video preview">
  <span class="video__name">LARKFIELD</span>
  <svg class="video__play" width="34" height="34" viewBox="0 0 38 38"><circle cx="19" cy="19" r="17" fill="#f2f2f2" stroke="#bbb" stroke-width="2"/><path d="M14 10l13 9-13 9z" fill="#111"/></svg>
</div>

<footer class="footer">
  <p class="footer__copy">© 2013 <span>Larkfieldadvisory</span>. All rights reserved</p>
  <div class="social" aria-label="Social links">
    <span class="social__item"></span><span class="social__item"></span><span class="social__item"></span><span class="social__item"></span><span class="social__item"></span>
  </div>
</footer>

</body>
</html>
```